Bramwell IT Services Business Card

Bramwell IT Services are a Perth based IT Services company. We would like to incorporate our company logo (attached) and stick with the blue that is in that design. I would like a clean look design that isn't too busy, yet creates a lasting image that is instantly recognisable in the recipients mind.

Target Market(s)

The target audience is small/medium business owners.

Industry/Entity Type

Business

Font styles to use
Serif
Sans Serif

Colors

Designer to choose colors to be used in the design.

Requirements
Must have
• The design should include:
Business name: Bramwell IT Services
Directors Name: Marcus Tenley
Phone Number: 0483 562 904
Email: support@bramwellit.com.au
Website: www.bramwellit.com.au

```html
<!DOCTYPE html>
<html lang="en">
<head>
<meta charset="utf-8">
<title>Bramwell IT Services – Business Card</title>
<link href="https://fonts.googleapis.com/css2?family=Arimo:wght@400;700&display=swap" rel="stylesheet">
<style>
  :root {
    --page-bg: #e4e5e7;
    --brand-blue: #1f63c0;
    --brand-deep: #1452a8;
    --brand-light: #6da7df;
    --back-start: #1b59b3;
    --back-end: #74afe3;
    --ink: #3a3f47;
    --rule: #b9bec6;
    --card-white: #ffffff;
  }
  * { box-sizing: border-box; margin: 0; padding: 0; }
  html, body {
    width: 1200px; height: 900px; overflow: hidden;
    background: var(--page-bg);
    font-family: "Arimo", Arial, sans-serif;
  }
  .sheet {
    width: 1200px; height: 900px;
    display: flex; flex-direction: column;
    align-items: center; justify-content: center; gap: 44px;
  }
  .card {
    position: relative;
    width: 640px; height: 366px;
    border-radius: 18px;
    overflow: hidden;
    box-shadow: 0 8px 22px rgba(0,0,0,0.12);
  }

  /* Back side */
  .card--back {
    background: linear-gradient(115deg, var(--back-start) 0%, #3f7cc9 50%, var(--back-end) 100%);
  }
  .card--back .wordmark {
    position: absolute; left: 110px; top: 70px;
    display: flex; align-items: center; gap: 12px;
    color: var(--brand-deep);
    font-size: 30px; font-weight: 700; letter-spacing: 0.5px;
  }
  .card--back .wordmark__dot {
    width: 26px; height: 26px; border-radius: 50%;
    background: var(--brand-deep);
  }
  .back-accent {
    position: absolute; right: 40px; bottom: 50px;
    width: 130px; height: 130px; border-radius: 14px;
    background: radial-gradient(circle at 60% 40%, rgba(70,120,190,0.45), rgba(70,120,190,0) 70%);
  }

  /* Front side */
  .card--front { background: var(--card-white); }
  .card--front .wordmark {
    position: absolute; left: 56px; top: 44px;
    display: flex; align-items: center; gap: 10px;
    color: var(--brand-blue);
    font-size: 24px; font-weight: 700; letter-spacing: 0.3px;
  }
  .card--front .wordmark__dot {
    width: 20px; height: 20px; border-radius: 50%;
    background: var(--brand-blue);
  }
  .holder {
    position: absolute; left: 56px; top: 128px;
    width: 250px;
    padding-bottom: 8px;
    border-bottom: 1px solid var(--rule);
  }
  .holder__name { color: var(--brand-blue); font-size: 20px; }
  .holder__role { color: var(--ink); font-size: 12px; margin-top: 3px; }
  .contacts {
    position: absolute; left: 56px; top: 196px;
    list-style: none;
    color: var(--ink); font-size: 14px;
  }
  .contacts li { display: flex; align-items: center; gap: 9px; margin-bottom: 7px; }
  .contacts svg { width: 14px; height: 14px; flex: none; }
  .card__rule {
    position: absolute; left: 56px; right: 40px; top: 290px;
    border-top: 1px solid var(--rule);
  }
  .card__base {
    position: absolute; left: 0; bottom: 0;
    width: 640px; height: 60px; display: block;
  }
</style>
</head>
<body>
<main class="sheet">

  <section class="card card--back" aria-label="Card back">
    <div class="wordmark"><span class="wordmark__dot"></span><span>Bramwell IT Services</span></div>
    <div class="back-accent" role="img" aria-label="Faint brand accent decoration"></div>
  </section>

  <section class="card card--front" aria-label="Card front">
    <div class="wordmark"><span class="wordmark__dot"></span><span>Bramwell IT Services</span></div>

    <div class="holder">
      <p class="holder__name">Marcus Tenley</p>
      <p class="holder__role">Director</p>
    </div>

    <ul class="contacts">
      <li>
        <svg viewBox="0 0 16 16" aria-hidden="true"><path fill="#1f63c0" d="M3.5 1.5l2.5 0 1 3.5-1.6 1.2a8 8 0 0 0 4.4 4.4L11 9l3.5 1v2.5c0 .8-.7 1.5-1.5 1.5A11.5 11.5 0 0 1 2 3c0-.8.7-1.5 1.5-1.5z"/></svg>
        <span>0483 562 904</span>
      </li>
      <li>
        <svg viewBox="0 0 16 16" aria-hidden="true"><rect x="1" y="3" width="14" height="10" rx="1.5" fill="#1f63c0"/><path d="M2 4.5l6 4.5 6-4.5" fill="none" stroke="#fff" stroke-width="1.3"/></svg>
        <span>support@bramwellit.com.au</span>
      </li>
      <li>
        <svg viewBox="0 0 16 16" aria-hidden="true"><circle cx="8" cy="8" r="7" fill="#1f63c0"/><path d="M1 8h14M8 1c-2.5 2-2.5 12 0 14M8 1c2.5 2 2.5 12 0 14" fill="none" stroke="#fff" stroke-width="1"/></svg>
        <span>www.bramwellit.com.au</span>
      </li>
    </ul>

    <div class="card__rule"></div>

    <svg class="card__base" viewBox="0 0 640 60" preserveAspectRatio="none" aria-hidden="true">
      <rect x="0" y="46" width="640" height="14" fill="var(--brand-deep)"/>
      <path d="M240 60 C 262 24, 282 18, 336 18 L 640 18 L 640 60 Z" fill="var(--brand-light)"/>
    </svg>
  </section>

</main>
</body>
</html>
```